Design a New Business Card for Our Company

We are looking for fresh, unique, and a modern business card that reflects our roots as digital marketing agency focused on SEM.

Industry/Entity Type

Marketing

Contact Information for Business Card

looking for very unique out of the box designs. clean and modern that compliments our logo

Requirements
Must have
• colors should match our logo
• Front should have name, address, email, and phone/fax of the person, phone/fax are the same number
• back should have our url

```html
<!DOCTYPE html>
<html lang="en">
<head>
<meta charset="utf-8">
<title>Brightpath Solutions – Business Card</title>
<link href="https://fonts.googleapis.com/css2?family=Open+Sans:wght@400;600;700&display=swap" rel="stylesheet">
<style>
  :root {
    --stage: #2b2b2d;
    --card-white: #f7f7f8;
    --card-white-edge: #e4e5e7;
    --brand-blue: #3d7fc8;
    --brand-blue-deep: #2f6bb0;
    --brand-blue-light: #5b97d6;
    --ink-grey: #6f7378;
    --ink-dark: #55595e;
    --logo-grey: #8d9298;
    --rule: #b9bcc0;
    --cloud: #c9dbef;
  }
  * { margin: 0; padding: 0; box-sizing: border-box; }
  html, body {
    width: 1200px; height: 997px; overflow: hidden;
    background: var(--stage);
    font-family: "Open Sans", Arial, sans-serif;
  }
  .canvas {
    width: 1200px; height: 997px;
    display: flex; flex-direction: column; align-items: center; justify-content: center;
    gap: 56px;
  }
  .card {
    width: 640px; height: 366px;
    border-radius: 22px;
    position: relative; overflow: hidden;
  }

  /* Front */
  .card--front {
    background: linear-gradient(160deg, #ffffff 0%, var(--card-white) 60%, var(--card-white-edge) 100%);
  }
  .brand {
    position: absolute; display: flex; align-items: center; gap: 10px;
    font-weight: 700; letter-spacing: -0.5px;
  }
  .brand__dot { border-radius: 50%; flex: none; }
  .card--front .brand { top: 34px; right: 44px; font-size: 40px; color: var(--logo-grey); }
  .card--front .brand__dot { width: 26px; height: 26px; background: var(--logo-grey); }
  .card--front .rule {
    position: absolute; top: 116px; left: 44px; right: 44px;
    height: 1px; background: var(--rule);
  }
  .url {
    position: absolute; right: 44px; bottom: 150px;
    font-size: 15px; font-weight: 700; color: var(--brand-blue);
  }
  .person { position: absolute; left: 44px; bottom: 30px; }
  .person__name { font-size: 22px; font-weight: 700; color: var(--ink-dark); line-height: 1.1; }
  .person__title { font-size: 13px; font-weight: 700; color: var(--brand-blue); letter-spacing: 0.5px; margin-bottom: 10px; }
  .contact { list-style: none; }
  .contact li {
    display: flex; align-items: center; gap: 10px;
    font-size: 14px; color: var(--ink-grey); line-height: 22px;
  }
  .contact__icon {
    width: 16px; height: 16px; border-radius: 50%;
    background: var(--ink-grey); flex: none;
    display: flex; align-items: center; justify-content: center;
  }
  .contact__icon svg { width: 10px; height: 10px; }

  /* Back */
  .card--back {
    background: linear-gradient(170deg, var(--brand-blue-light) 0%, var(--brand-blue) 55%, var(--brand-blue-deep) 100%);
  }
  .card--back .brand {
    top: 36px; left: 50%; transform: translateX(-50%);
    font-size: 40px; color: #ffffff; white-space: nowrap;
  }
  .card--back .brand__dot { width: 26px; height: 26px; background: #ffffff; }
  .keyword-art {
    position: absolute; left: 150px; top: 118px; width: 370px; height: 212px;
    border-radius: 10px;
    background: radial-gradient(ellipse at center, var(--cloud) 0%, rgba(201,219,239,0.55) 55%, rgba(201,219,239,0) 100%);
  }
</style>
</head>
<body>
<main class="canvas">

  <section class="card card--front" aria-label="Business card front">
    <div class="brand"><span class="brand__dot"></span><span class="brand__name">brightpath</span></div>
    <div class="rule"></div>
    <p class="url">www.brightpathsol.com</p>
    <div class="person">
      <h1 class="person__name">Maren Holloway</h1>
      <p class="person__title">FOUNDER &amp; CEO</p>
      <ul class="contact">
        <li><span class="contact__icon"><svg viewBox="0 0 10 10"><path d="M2 1.5 L3.6 1.5 L4.2 3.4 L3.2 4.2 Q4 5.9 5.8 6.8 L6.6 5.8 L8.5 6.4 L8.5 8 Q4.5 8.4 2 4.5 Z" fill="#fff"/></svg></span>0561 204 387</li>
        <li><span class="contact__icon"><svg viewBox="0 0 10 10"><rect x="2" y="2" width="6" height="6" rx="1" fill="#fff"/><rect x="3.2" y="3.2" width="3.6" height="1.4" fill="#6f7378"/></svg></span>0172 903 518</li>
        <li><span class="contact__icon"><svg viewBox="0 0 10 10"><rect x="1.5" y="2.5" width="7" height="5" fill="#fff"/><path d="M1.5 2.5 L5 5.5 L8.5 2.5" stroke="#6f7378" stroke-width="0.8" fill="none"/></svg></span>care@northwindmail.com</li>
        <li><span class="contact__icon"><svg viewBox="0 0 10 10"><path d="M5 1.3 A2.6 2.6 0 0 1 7.6 3.9 Q7.6 5.6 5 8.7 Q2.4 5.6 2.4 3.9 A2.6 2.6 0 0 1 5 1.3 Z" fill="#fff"/><circle cx="5" cy="3.9" r="0.9" fill="#6f7378"/></svg></span>Rm 4, Larkfield, Oak St<br>Canada</li>
      </ul>
    </div>
  </section>

  <section class="card card--back" aria-label="Business card back">
    <div class="brand"><span class="brand__dot"></span><span class="brand__name">brightpath</span></div>
    <div class="keyword-art" role="img" aria-label="Word cloud of marketing keywords forming the letters SEM with a magnifying glass"></div>
  </section>

</main>
</body>
</html>
```